Website Design for Videographer

I am looking to update my website - www.brinolvaske.com. I am a wedding videographer who specialises in natural and documentary videography.

The website will be built by my designer using the Wordpress Plinthworx framework.

Requirements;
I want the website to have a clean white look mixed in with video footage.
Needs to be classy. At the moment my website uses a lot of Gold. On the new look I DO NOT want gold.

Need a web and mobile design for the following 12 pages;

* Home page (need to have example videos and text)
* About (this is about me and my service)
* Videos (examples of my work)
* Testimonials
* Packages
* Contact
* Content (this is to show social media content that I am making in a vertical format and advertise this service).
* Blog (index page for blog)
* Blog pages (individual pages for blog content)
* Wedding Venues Index Page (https://brinolvaske.com/north-east-wedding-venues/)
* Individual venue pages (https://brinolvaske.com/north-east-wedding-venues/marlow-tendle-lodge-wedding-videos/) - Needs to show videos, photos, text as is on the current page.
* Venue Tours (https://brinolvaske.com/wedding-venue-tours/)

My current logo is attached however on the website I want to go for a black and white style for it.

Example styles I like however must not be copied.
https://joswelbrant.co.uk/about/
https://oakandripple.co.uk/ (if done in white)
https://tumblemothpictures.co.uk/

Target Market(s)

Couples getting married aged 25-35

Industry/Entity Type

Weddings

Number of Pages Required

5+ page

Font styles to use
Sans Serif

Requirements
Must have
• A classy look, black and white, use videos and photos.
Should not have
• Gold colour

```html
<!DOCTYPE html>
<html lang="en">
<head>
<meta charset="utf-8">
<title>Brin Olvaske Wedding Films – North East Wedding Videographer</title>
<link rel="stylesheet" href="https://fonts.googleapis.com/css2?family=Cinzel:wght@400&family=Poppins:wght@400;500&display=swap">
<style>
:root{
  --ink:#111111;
  --white:#ffffff;
  --mist:#f4f4f4;
  --soft-grey:#8c8c8c;
  --body:#2b2b2b;
  --night:#272624;
  --footer:#6b6869;
  --line-light:rgba(255,255,255,.7);
}
*{box-sizing:border-box;margin:0;padding:0}
html,body{width:1200px;height:5159px;overflow:hidden;background:var(--white)}
body{font-family:"Poppins",sans-serif;color:var(--ink);position:relative}
.serif{font-family:"Cinzel",serif;font-weight:400}

/* header */
.site-header{position:absolute;top:0;left:0;width:1200px;height:124px;background:var(--white)}
.nav{position:absolute;top:52px;display:flex;gap:38px;font-size:11.5px;text-transform:uppercase;letter-spacing:.2px}
.nav-left{left:68px}
.nav-right{left:768px}
.brand{position:absolute;left:0;width:1200px;top:26px;text-align:center;font-family:"Poppins",sans-serif;font-weight:500;color:var(--ink)}
.brand-mark{display:block;width:40px;height:40px;border:2px solid var(--ink);margin:0 auto 8px}
.brand-name{display:block;font-size:19px;letter-spacing:5px;line-height:20px}
.brand-sub{display:block;font-size:9px;letter-spacing:6px;line-height:14px}
.btn-enquire{position:absolute;left:996px;top:34px;width:136px;height:46px;background:var(--ink);color:var(--white);font-size:13px;font-weight:500;display:flex;align-items:center;justify-content:center}

/* hero */
.hero-intro{position:absolute;top:124px;left:0;width:1200px;height:346px;background:var(--mist);text-align:center}
.hero-title{position:absolute;top:100px;left:0;width:1200px;font-size:58px;line-height:64px;letter-spacing:1px}
.btn-book{position:absolute;left:470px;top:248px;width:258px;height:60px;background:var(--ink);color:var(--white);font-size:15px;font-weight:500;display:flex;align-items:center;justify-content:center;padding-left:40px}
.btn-book::before{content:"";position:absolute;left:14px;top:16px;width:28px;height:28px;border:2px solid var(--white)}
.hero-photo{position:absolute;top:470px;left:0;width:1200px;height:640px;background:linear-gradient(180deg,#cfd3cf 0%,#6f8a62 35%,#3f5a33 65%,#2c3f24 100%)}

/* videos */
.section-title{position:absolute;left:0;width:1200px;text-align:center;font-size:54px;letter-spacing:1px}
.section-title .dim{color:var(--soft-grey)}
.section-sub{position:absolute;left:0;width:1200px;text-align:center;font-size:29px;font-weight:500}
.intro-copy{position:absolute;left:90px;width:1020px;top:1390px;text-align:center;font-size:14.2px;line-height:28px;color:var(--body)}
.video-grid{position:absolute;left:70px;top:1580px;display:grid;grid-template-columns:repeat(3,337px);column-gap:27px;row-gap:32px}
.video-tile{width:337px;height:337px;position:relative}
.play{position:absolute;left:50%;top:50%;width:56px;height:56px;margin:-28px 0 0 -28px}

/* story band */
.story{position:absolute;top:3170px;left:0;width:1200px;height:648px;background:radial-gradient(ellipse at 50% 40%,#3d3a36 0%,var(--night) 70%);color:var(--white)}
.story-frame{position:absolute;left:68px;top:72px;width:1064px;height:472px;border:2px solid var(--line-light);border-bottom:none}
.story-frame::before,.story-frame::after{content:"";position:absolute;bottom:0;height:2px;background:var(--line-light)}
.story-frame::before{left:-2px;width:380px}
.story-frame::after{right:-2px;width:380px}
.story-title{position:absolute;top:148px;left:0;width:1200px;text-align:center;font-size:48px;line-height:82px;letter-spacing:1px}
.story-copy{position:absolute;top:328px;left:90px;width:1020px;text-align:center;font-size:14px;line-height:32px}
.btn-light{position:absolute;left:460px;top:512px;width:278px;height:60px;background:var(--white);color:var(--ink);font-size:21px;font-weight:500;display:flex;align-items:center;justify-content:center;padding-left:40px}
.btn-light::before{content:"";position:absolute;left:6px;top:14px;width:30px;height:30px;border:2px solid var(--white);background:var(--night)}

/* styled shoots */
.shoot{position:absolute;top:4132px;width:510px;height:434px}
.carousel-btn{position:absolute;top:4638px;width:64px;height:64px;border-radius:50%;display:flex;align-items:center;justify-content:center}
.carousel-prev{left:530px;border:1.5px solid #9a9a9a;background:var(--white)}
.carousel-next{left:604px;background:var(--ink)}

/* footer */
.site-footer{position:absolute;top:4794px;left:0;width:1200px;height:365px;background:var(--footer);color:var(--white)}
.footer-brand{position:absolute;top:56px;left:0;width:1200px;text-align:center;font-weight:500}
.footer-brand .brand-mark{border-color:var(--white)}
.footer-rule{position:absolute;top:136px;height:1px;background:rgba(255,255,255,.7);width:380px}
.footer-nav{position:absolute;top:204px;left:0;width:1200px;display:flex;justify-content:center;align-items:center;gap:40px;font-size:11.5px;text-transform:uppercase}
.footer-nav .boxed{border:1.5px solid var(--white);padding:15px 36px;font-size:13px}
.footer-base{position:absolute;top:286px;left:68px;width:1064px;height:1px;background:rgba(255,255,255,.7)}
.copyright{position:absolute;top:312px;left:66px;font-size:9.5px}
.social{position:absolute;top:300px;left:982px;display:flex;gap:20px}
.social span{width:38px;height:38px;border-radius:50%;border:1.5px solid var(--white);display:block}
.social span:first-child{background:var(--white)}
</style>
</head>
<body>

<header class="site-header">
  <nav class="nav nav-left"><span>Home</span><span>About Brin</span><span>Wedding Films</span><span>Blog</span></nav>
  <div class="brand"><span class="brand-mark"></span><span class="brand-name">BRIN OLVASKE</span><span class="brand-sub">WEDDING FILMS</span></div>
  <nav class="nav nav-right" style="gap:76px"><span>Testimonials</span><span>Packages</span></nav>
  <a class="btn-enquire">ENQUIRE</a>
</header>

<section class="hero-intro">
  <h1 class="hero-title serif">NORTH EAST WEDDING<br>VIDEOGRAPHER</h1>
  <a class="btn-book">BOOK WITH ME</a>
</section>
<div class="hero-photo" role="img" aria-label="Bride and groom embracing beside a lake surrounded by ferns and pine trees"></div>

<h2 class="section-title serif" style="top:1206px">OUR WEDDING <span class="dim">VIDEOS</span></h2>
<p class="section-sub" style="top:1322px">FOR COUPLES WHO LIKE TO KEEP IT REAL!</p>
<p class="intro-copy">My videography style is ideal for couples who want to spend time with their guests instead of posing. I focus on capturing the genuine moments and emotions throughout your wedding day. This approach allows you to enjoy your special day without constant interruptions for staged shots. I blend into the background, ensuring your wedding film reflects the authentic joy and celebration of the occasion. This way, you can focus on making memories with your loved ones while I handle the storytelling.</p>

<div class="video-grid">
  <div class="video-tile" role="img" aria-label="Couple outside a stone church" style="background:linear-gradient(160deg,#4a5244,#8e8f86 60%,#c9c7c0)"><svg class="play" viewBox="0 0 56 56"><circle cx="28" cy="28" r="26" fill="none" stroke="#fff" stroke-width="3"/><path d="M22 17 L39 28 L22 39Z" fill="#fff"/></svg></div>
  <div class="video-tile" role="img" aria-label="Bride portrait in a vintage car" style="background:linear-gradient(160deg,#3e4a30,#b9a58e 55%,#e6ddd2)"><svg class="play" viewBox="0 0 56 56"><circle cx="28" cy="28" r="26" fill="none" stroke="#fff" stroke-width="3"/><path d="M22 17 L39 28 L22 39Z" fill="#fff"/></svg></div>
  <div class="video-tile" role="img" aria-label="Couple walking hand in hand, groom in blue suit" style="background:linear-gradient(160deg,#6d8a55,#2f4fa0 50%,#d9d3ca)"><svg class="play" viewBox="0 0 56 56"><circle cx="28" cy="28" r="26" fill="none" stroke="#fff" stroke-width="3"/><path d="M22 17 L39 28 L22 39Z" fill="#fff"/></svg></div>
  <div class="video-tile" role="img" aria-label="Couple exchanging rings during ceremony" style="background:linear-gradient(160deg,#5b5a63,#a99a86 55%,#3a3430)"><svg class="play" viewBox="0 0 56 56"><circle cx="28" cy="28" r="26" fill="none" stroke="#fff" stroke-width="3"/><path d="M22 17 L39 28 L22 39Z" fill="#fff"/></svg></div>
  <div class="video-tile" role="img" aria-label="Bride hugging a laughing guest" style="background:linear-gradient(160deg,#3c4438,#b4aea4 50%,#2c2f36)"><svg class="play" viewBox="0 0 56 56"><circle cx="28" cy="28" r="26" fill="none" stroke="#fff" stroke-width="3"/><path d="M22 17 L39 28 L22 39Z" fill="#fff"/></svg></div>
  <div class="video-tile" role="img" aria-label="Couple embracing by a lake" style="background:linear-gradient(180deg,#cdd1cc,#6a8559 45%,#2e4227)"><svg class="play" viewBox="0 0 56 56"><circle cx="28" cy="28" r="26" fill="none" stroke="#fff" stroke-width="3"/><path d="M22 17 L39 28 L22 39Z" fill="#fff"/></svg></div>
  <div class="video-tile" role="img" aria-label="Couple pouring a champagne tower" style="background:linear-gradient(160deg,#3d5a32,#a7a39a 50%,#1f1f22)"><svg class="play" viewBox="0 0 56 56"><circle cx="28" cy="28" r="26" fill="none" stroke="#fff" stroke-width="3"/><path d="M22 17 L39 28 L22 39Z" fill="#fff"/></svg></div>
  <div class="video-tile" role="img" aria-label="Couple kissing beside a classic car" style="background:linear-gradient(160deg,#3c5a33,#2b3a47 50%,#d9cfc7)"><svg class="play" viewBox="0 0 56 56"><circle cx="28" cy="28" r="26" fill="none" stroke="#fff" stroke-width="3"/><path d="M22 17 L39 28 L22 39Z" fill="#fff"/></svg></div>
  <div class="video-tile" role="img" aria-label="Bride walking down the aisle under festoon lights" style="background:linear-gradient(160deg,#c8bfae,#7d7467 50%,#2e2c2f)"><svg class="play" viewBox="0 0 56 56"><circle cx="28" cy="28" r="26" fill="none" stroke="#fff" stroke-width="3"/><path d="M22 17 L39 28 L22 39Z" fill="#fff"/></svg></div>
  <div class="video-tile" role="img" aria-label="Couple smiling in a garden" style="background:linear-gradient(160deg,#4f6a3d,#d8d4cd 50%,#1d1e22)"><svg class="play" viewBox="0 0 56 56"><circle cx="28" cy="28" r="26" fill="none" stroke="#fff" stroke-width="3"/><path d="M22 17 L39 28 L22 39Z" fill="#fff"/></svg></div>
  <div class="video-tile" role="img" aria-label="Couple by a bright window" style="background:linear-gradient(90deg,#e7e6e2,#8f8a82 45%,#3a3633)"><svg class="play" viewBox="0 0 56 56"><circle cx="28" cy="28" r="26" fill="none" stroke="#fff" stroke-width="3"/><path d="M22 17 L39 28 L22 39Z" fill="#fff"/></svg></div>
  <div class="video-tile" role="img" aria-label="Groom and bride in tiara close together" style="background:linear-gradient(160deg,#3e5a34,#55627e 50%,#c9b8a6)"><svg class="play" viewBox="0 0 56 56"><circle cx="28" cy="28" r="26" fill="none" stroke="#fff" stroke-width="3"/><path d="M22 17 L39 28 L22 39Z" fill="#fff"/></svg></div>
</div>

<section class="story" role="img" aria-label="Dimmed background of guests laughing at a reception">
  <div class="story-frame"></div>
  <h2 class="story-title serif">YOUR WEDDING HAS A STORY.<br>RELIVE YOUR MOMENTS FOR A LIFETIME.</h2>
  <p class="story-copy">There's a whole gamut of emotions wrapped up in your wedding day bubble. So don't risk forgetting the sounds as well as the sights. The giggles, the vows, the jokes, the speeches, and the music add atmosphere to your wedding video and bring your day back to life each and every time you watch it. Memories of what was said, a certain person's signature laugh, and the dodgy Dad jokes will fade over time. So imagine how special it will be 20 years on to enjoy your own film with your next generation and be reminded of those extra special sounds again.</p>
  <a class="btn-light">ENQUIRE</a>
</section>

<h2 class="section-title serif" style="top:3928px">STYLED <span class="dim">SHOOTS</span></h2>
<p class="section-sub" style="top:4026px">FILMED IN JOSHUA TREE &amp; COACHELLA. CALIFORNIA</p>
<div class="shoot" style="left:68px;background:linear-gradient(160deg,#4d5f3f,#8b8a86 40%,#2c3550 75%,#1f5a44)" role="img" aria-label="Wedding party group portrait on stone steps"><svg class="play" viewBox="0 0 56 56"><circle cx="28" cy="28" r="26" fill="none" stroke="#fff" stroke-width="3"/><path d="M22 17 L39 28 L22 39Z" fill="#fff"/></svg></div>
<div class="shoot" style="left:620px;background:linear-gradient(160deg,#c9c3b6,#3b3f4e 45%,#e6e2db)" role="img" aria-label="Guest dancing energetically at the reception"><svg class="play" viewBox="0 0 56 56"><circle cx="28" cy="28" r="26" fill="none" stroke="#fff" stroke-width="3"/><path d="M22 17 L39 28 L22 39Z" fill="#fff"/></svg></div>
<a class="carousel-btn carousel-prev" aria-label="Previous"><svg width="18" height="18" viewBox="0 0 18 18"><path d="M11 3 L5 9 L11 15" fill="none" stroke="#444" stroke-width="2"/></svg></a>
<a class="carousel-btn carousel-next" aria-label="Next"><svg width="18" height="18" viewBox="0 0 18 18"><path d="M7 3 L13 9 L7 15" fill="none" stroke="#fff" stroke-width="2.4"/></svg></a>

<footer class="site-footer">
  <div class="footer-brand"><span class="brand-mark"></span><span class="brand-name">BRIN OLVASKE</span><span class="brand-sub">WEDDING FILMS</span></div>
  <div class="footer-rule" style="left:68px"></div>
  <div class="footer-rule" style="left:752px"></div>
  <nav class="footer-nav"><span>Home</span><span>About Brin</span><span>Wedding Films</span><span class="boxed">Enquire</span><span>Blog</span><span>Testimonials</span><span>Packages</span></nav>
  <div class="footer-base"></div>
  <p class="copyright">Copyright 2010 - 2024 © Brin Olvaske Wedding Films Limited. All Rights Reserved</p>
  <div class="social" aria-label="Social links"><span></span><span></span><span></span></div>
</footer>

</body>
</html>
```